Business Card design which attached logo. Company is called Crestline Shield and main colours are Orange & Black.

Company specialises in Paint Protection and Detailing for supercars.

Details needed on business card:

Sales

Address: Unit 14, 517 Hadley Road, Fernvale Heights, NSW 2847

Phone: 02 6194 2738

website: www.crestlineshield.com.au

Email: sales@crestlineshield.com.au

```html
<!DOCTYPE html>
<html lang="en">
<head>
<meta charset="utf-8">
<title>Crestline Shield — Business Card</title>
<link rel="stylesheet" href="https://fonts.googleapis.com/css2?family=Quicksand:wght@400;500&display=swap">
<style>
  :root {
    --backdrop: #26282c;
    --ink: #0b0b0c;
    --paper: #ffffff;
    --orange: #f0582a;
    --orange-soft: #f47a52;
    --grey-text: #6e6e72;
    --faint-line: #2b2b2e;
  }
  * { margin: 0; padding: 0; box-sizing: border-box; }
  html, body {
    width: 1200px; height: 900px; overflow: hidden;
    background: var(--backdrop);
    font-family: "Quicksand", sans-serif;
  }
  .canvas {
    position: relative; width: 1200px; height: 900px;
    display: flex; align-items: center; justify-content: center; gap: 40px;
  }
  .card {
    position: relative; width: 540px; height: 309px;
    background: var(--ink); overflow: hidden;
    box-shadow: 0 14px 30px rgba(0,0,0,.45);
  }
  .card-front .wave { position: absolute; inset: 0; width: 100%; height: 100%; }
  .brand-name {
    position: absolute; left: 40px; top: 56px;
    color: var(--orange); font-weight: 400; font-size: 22px;
    letter-spacing: 3px; text-transform: uppercase;
  }
  .contact {
    position: absolute; right: 18px; top: 132px;
    text-align: right; font-weight: 400;
  }
  .person-name {
    color: var(--orange); font-size: 21px; letter-spacing: 1.5px;
    text-transform: uppercase; margin-bottom: 8px;
  }
  .address {
    color: var(--orange-soft); font-size: 12.5px; line-height: 1.35;
    margin-right: 24px; margin-bottom: 12px;
  }
  .contact-line {
    display: flex; align-items: center; justify-content: flex-end; gap: 9px;
    color: var(--grey-text); font-size: 12.5px; line-height: 1; margin-bottom: 8px;
  }
  .contact-line svg { width: 15px; height: 15px; flex: none; }
  .card-back .ring {
    position: absolute; left: 50%; top: 50%;
    width: 250px; height: 250px; margin: -125px 0 0 -125px;
    border: 2px solid var(--faint-line); border-radius: 50%;
  }
  .back-mark {
    position: absolute; left: 0; right: 0; top: 50%; transform: translateY(-50%);
    display: flex; align-items: center; justify-content: center; gap: 8px;
    color: var(--orange); font-size: 13px; letter-spacing: 2.5px; text-transform: uppercase;
  }
  .back-mark .dot {
    width: 12px; height: 12px; border: 1.5px solid var(--orange); border-radius: 50%;
  }
</style>
</head>
<body>
<main class="canvas">
  <section class="card card-front" aria-label="Business card front">
    <svg class="wave" viewBox="0 0 540 309" preserveAspectRatio="none" aria-hidden="true">
      <path d="M0,268 C150,258 250,128 540,102 L540,309 L0,309 Z" fill="var(--paper)"/>
      <path d="M0,244 C140,232 240,106 540,80 L540,90 C245,116 150,246 0,258 Z" fill="var(--orange)"/>
    </svg>
    <div class="brand-name">Crestline Shield</div>
    <div class="contact">
      <div class="person-name">Daniel Reyes</div>
      <div class="address">Unit 14, 517 Hadley Road<br>Fernvale Heights, NSW 2847</div>
      <div class="contact-line">02 6194 2738
        <svg viewBox="0 0 24 24"><path fill="var(--orange)" d="M6.6 10.8a15 15 0 0 0 6.6 6.6l2.2-2.2a1 1 0 0 1 1-.25 11.4 11.4 0 0 0 3.6.57 1 1 0 0 1 1 1V20a1 1 0 0 1-1 1A17 17 0 0 1 3 4a1 1 0 0 1 1-1h3.5a1 1 0 0 1 1 1c0 1.25.2 2.45.57 3.570a1 1 0 0 1-.25 1z"/></svg>
      </div>
      <div class="contact-line">sales@crestlineshield.com.au
        <svg viewBox="0 0 24 24"><rect x="2" y="5" width="20" height="14" rx="1" fill="var(--orange)"/><path d="M3 6l9 7 9-7" fill="none" stroke="#fff" stroke-width="1.6"/></svg>
      </div>
      <div class="contact-line">www.crestlineshield.com.au
        <svg viewBox="0 0 24 24"><circle cx="12" cy="12" r="10" fill="var(--orange)"/><g fill="none" stroke="#fff" stroke-width="1.3"><ellipse cx="12" cy="12" rx="4" ry="10"/><path d="M2 12h20M4 7h16M4 17h16"/></g></svg>
      </div>
    </div>
  </section>

  <section class="card card-back" aria-label="Business card back">
    <div class="ring"></div>
    <div class="back-mark"><span class="dot"></span>Crestline Shield</div>
  </section>
</main>
</body>
</html>
```